Tellmora Corporate Stationery

Look for design of all new corporate stationery for an existing insurance broking business that is going through a redesign and move from older partners to younger family members. New Logo is attached. Company is Brisbane based.
Colours in the Logo is Hex #43bed8 and website features a lot of hex #17b8d8. Website front page "A plan to protect you" - headline. "Professional and Individual advice to protect your greatest assets" - tagline.

Stationery required: Business Cards, Letter head, Thank-you cards, Birthday cards, Presentation folders, With Compliment slips and a powerpoint template. We also would like to send a card to all customers with the something along of the lines of "something new".

Target Market(s)

Customers of Insurance business looking at superannuation, life and income protection insurance, investment advice and wills

Industry/Entity Type

Insurance Broker

Font styles to use
Other font styles liked:
• same as logo

Requirements
Must have
• The above designs for new stationery for the new business including:
• Business Cards, Letter head, Thank-you cards, Birthday cards, Presentation folders, With Compliment slips and a powerpoint template. We also would like to send a card to all customers with the something along of the lines of "something new".
Nice to have
• It is a new look - long time family business being passed to next generation - big focus on advice for YOU, individual advice etc..

```html
<!DOCTYPE html>
<html lang="en">
<head>
<meta charset="utf-8">
<title>Tellmora Business Card</title>
<link rel="stylesheet" href="https://fonts.googleapis.com/css2?family=Open+Sans:wght@300;400;500&display=swap">
<style>
  :root{
    --brand-cyan:#40bed8;
    --brand-grey:#838487;
    --paper:#ffffff;
    --page:#ffffff;
  }
  *{margin:0;padding:0;box-sizing:border-box}
  html,body{width:1200px;height:1000px;overflow:hidden;background:var(--page)}
  body{position:relative;font-family:"Open Sans",Arial,sans-serif}
  .card{position:absolute;left:206px;width:787px;height:486px;background:var(--brand-cyan);overflow:hidden;box-shadow:3px 3px 6px rgba(0,0,0,.18)}
  .card--front{top:0}
  .card--back{top:514px}
  .card svg.card-shapes{position:absolute;inset:0}
  .brand-name{position:absolute;left:127px;top:272px;width:533px;text-align:center;color:var(--brand-cyan);font-weight:500;line-height:1}
  .brand-name__main{display:block;font-size:66px;letter-spacing:4px;text-transform:uppercase}
  .brand-name__sub{display:block;font-size:30px;letter-spacing:3px;text-transform:uppercase;margin-top:10px}
  .contact-text{position:absolute;top:96px;writing-mode:vertical-rl;color:var(--paper);font-size:17.5px;letter-spacing:.6px;line-height:34px;white-space:nowrap}
  .person{position:absolute;right:78px;top:70px;writing-mode:vertical-rl;color:var(--paper);font-weight:300;white-space:nowrap}
  .person__name{font-size:62px;line-height:66px;letter-spacing:1px}
  .person__role{font-size:31px;line-height:44px;letter-spacing:1px}
</style>
</head>
<body>

<section class="card card--front">
  <svg class="card-shapes" width="787" height="486" viewBox="0 0 787 486">
    <polygon class="diagonal-band" points="0,405 654,0 734,0 0,453" fill="var(--paper)"/>
    <circle class="brand-disc" cx="388" cy="188" r="120" fill="var(--paper)"/>
    <rect class="brand-plaque" x="127" y="272" width="533" height="82" rx="10" fill="var(--paper)"/>
    <rect class="brand-plaque" x="168" y="340" width="452" height="52" rx="14" fill="var(--paper)"/>
  </svg>
  <div class="brand-name">
    <span class="brand-name__main">Tellmora</span>
    <span class="brand-name__sub">Financial Group</span>
  </div>
</section>

<section class="card card--back">
  <svg class="card-shapes" width="787" height="486" viewBox="0 0 787 486">
    <rect class="center-band" x="339" y="0" width="109" height="486" fill="var(--paper)"/>
    <rect class="center-disc" x="232" y="141" width="322" height="205" rx="102" fill="var(--paper)"/>
    <g class="contact-pills" fill="var(--brand-grey)">
      <rect x="26" y="20" width="34" height="446" rx="17"/>
      <rect x="77" y="20" width="34" height="446" rx="17"/>
      <rect x="128" y="20" width="34" height="446" rx="17"/>
      <rect x="180" y="20" width="34" height="446" rx="17"/>
    </g>
    <g class="icon icon-web">
      <circle cx="43" cy="60" r="20" fill="var(--paper)"/>
      <circle cx="43" cy="60" r="14" fill="none" stroke="var(--brand-grey)" stroke-width="2"/>
      <ellipse cx="43" cy="60" rx="6" ry="14" fill="none" stroke="var(--brand-grey)" stroke-width="1.6"/>
      <line x1="29" y1="60" x2="57" y2="60" stroke="var(--brand-grey)" stroke-width="1.6"/>
    </g>
    <g class="icon icon-mail">
      <rect x="78" y="40" width="32" height="42" rx="2" fill="var(--paper)"/>
      <polyline points="81,44 94,61 107,44" fill="none" stroke="var(--brand-grey)" stroke-width="2"/>
      <polyline points="81,78 94,61 107,78" fill="none" stroke="var(--brand-grey)" stroke-width="2"/>
    </g>
    <g class="icon icon-phone">
      <rect x="122" y="50" width="46" height="20" rx="8" fill="var(--paper)"/>
      <rect x="136" y="48" width="18" height="24" rx="4" fill="var(--brand-grey)"/>
      <rect x="140" y="52" width="10" height="16" rx="2" fill="var(--paper)"/>
    </g>
    <g class="icon icon-home">
      <polygon points="176,42 206,42 219,60 206,78 176,78" fill="var(--paper)"/>
      <polygon points="184,60 196,50 208,60 204,60 204,70 188,70 188,60" fill="var(--brand-grey)"/>
      <rect x="193" y="63" width="6" height="7" fill="var(--paper)"/>
    </g>
  </svg>
  <p class="contact-text" style="left:26px">www.tellmorafinancesite.com</p>
  <p class="contact-text" style="left:77px">contact@tellmorafinancesite.com</p>
  <p class="contact-text" style="left:128px">(07) 5550 1842</p>
  <p class="contact-text" style="left:180px">48 Harbourline Rd. Brisbane</p>
  <div class="person">
    <h1 class="person__name">Mara Quill</h1>
    <p class="person__role">Financial Advisor</p>
  </div>
</section>

</body>
</html>
```